New website for concierge mobile medical service

new website for business:
WEBSITE REQUEST LIST:
Luxury product look.
Professional. Clean & simple, NO stock people photos. Graphics OK.
Black and white text.

```html
<!DOCTYPE html>
<html lang="en">
<head>
<meta charset="utf-8">
<title>Lumen Health – Our Service Area</title>
<link href="https://fonts.googleapis.com/css2?family=Lato:wght@400;700;900&display=swap" rel="stylesheet">
<style>
:root{
  --ink:#1d1d1f;
  --white:#ffffff;
  --accent:#5b5aa8;
  --hero-dark:#03090d;
  --hero-blue:#0a3a5c;
  --map-grey:#676767;
  --map-grey-light:#7a7a7a;
  --band-deep:#14607f;
  --button:#88d0d8;
  --footer:#1e1e1e;
  --field-border:#cfcfcf;
}
*{box-sizing:border-box;margin:0;padding:0}
html,body{width:818px;height:1200px;overflow:hidden;background:var(--white)}
body{font-family:'Lato',sans-serif;color:var(--ink);position:relative}
.site-header{position:absolute;top:0;left:0;width:818px;height:73px;background:var(--white);z-index:2}
.brand{position:absolute;left:106px;top:12px;width:86px;height:86px;border-radius:50%;background:var(--white);display:flex;align-items:center;justify-content:center;z-index:3}
.brand-mark{width:76px;height:76px;border-radius:50%;background:#0d2a3f;border:4px solid #5fc3d6;display:flex;align-items:center;justify-content:center;text-align:center;color:var(--white);font-weight:700;font-size:10px;line-height:1.2;padding:0 6px}
.phone{position:absolute;right:98px;top:11px;display:flex;align-items:center;gap:8px;color:var(--accent);font-weight:700;font-size:13.5px}
.phone-icon{width:22px;height:22px;background:var(--accent);border-radius:2px;display:flex;align-items:center;justify-content:center}
.main-nav{position:absolute;right:98px;top:50px;display:flex}
.main-nav a{font-size:8.6px;font-weight:900;color:var(--ink);text-decoration:none;padding:0 12px;height:23px;line-height:14px;position:relative}
.main-nav a:last-child{padding-right:0}
.main-nav a.active{color:var(--accent)}
.main-nav a.active::after{content:"";position:absolute;left:0;right:0;bottom:0;height:3px;background:var(--hero-blue)}
.hero{position:absolute;top:73px;left:0;width:818px;height:180px;background:linear-gradient(90deg,var(--hero-dark) 0%,#06263b 45%,var(--hero-blue) 100%)}
.hero h1{position:absolute;left:98px;top:72px;color:var(--white);font-weight:900;font-size:31px;letter-spacing:.3px}
.hero-badge{position:absolute;left:590px;top:21px}
.intro{position:absolute;top:284px;left:0;width:818px;text-align:center}
.intro h2{font-size:19px;font-weight:700;color:#2a2a2a}
.intro p{font-size:12px;margin-top:10px;color:#2a2a2a}
.zip-search{position:absolute;top:347px;left:276px;display:flex;align-items:center;gap:11px}
.zip-search label{font-weight:700;font-size:11.5px;color:#2a2a2a}
.zip-search input{width:143px;height:28px;border:1px solid var(--field-border);border-radius:2px;padding:0 7px;font-family:inherit;font-size:9.5px;color:#333}
.coverage-map{position:absolute;left:158px;top:398px;width:502px;height:494px;border-radius:6px;background:linear-gradient(160deg,var(--map-grey-light) 0%,var(--map-grey) 100%)}
.subscribe{position:absolute;top:935px;left:0;width:818px;height:172px;background:linear-gradient(120deg,#1b8aa6 0%,var(--band-deep) 50%,#1a86a4 100%)}
.subscribe h2{position:absolute;top:28px;width:100%;text-align:center;color:var(--white);font-size:22px;font-weight:700}
.subscribe input{position:absolute;top:71px;width:217px;height:30px;border:0;padding:0 10px;font-family:inherit;font-size:8.5px;color:#333}
.subscribe .field-name{left:188px}
.subscribe .field-email{left:413px}
.subscribe button{position:absolute;top:107px;left:188px;width:442px;height:30px;border:0;background:var(--button);color:var(--white);font-family:inherit;font-size:11px;font-weight:700}
.site-footer{position:absolute;top:1107px;left:0;width:818px;height:93px;background:var(--footer);color:var(--white);text-align:center}
.footer-nav{display:flex;justify-content:center;gap:27px;margin-top:15px}
.footer-nav a{color:var(--white);font-size:8.6px;font-weight:900;text-decoration:none}
.copyright{font-size:7.4px;margin-top:12px}
.social{display:flex;justify-content:center;gap:12px;margin-top:10px}
.social span{width:11px;height:11px;border-radius:50%;background:var(--white)}
input::placeholder{color:#333}
</style>
</head>
<body>
<header class="site-header">
  <div class="brand"><div class="brand-mark">Lumen Health</div></div>
  <div class="phone">
    <span class="phone-icon"><svg width="12" height="12" viewBox="0 0 24 24"><path fill="#fff" d="M6.6 10.8a15 15 0 006.6 6.6l2.2-2.2a1 1 0 011-.25 11.4 11.4 0 003.6.6 1 1 0 011 1V20a1 1 0 01-1 1A17 17 0 013 4a1 1 0 011-1h3.5a1 1 0 011 1c0 1.25.2 2.45.6 3.6a1 1 0 01-.25 1z"/></svg></span>
    555-010-0199
  </div>
  <nav class="main-nav">
    <a href="#">HOME</a><a href="#">ABOUT US</a><a href="#">WHY LUMEN?</a><a href="#">SERVICE AREA</a><a href="#">OTHER</a><a href="#" class="active">FAQ</a><a href="#">CONTACT US</a>
  </nav>
</header>

<section class="hero">
  <h1>OUR SERVICE AREA</h1>
  <svg class="hero-badge" width="140" height="140" viewBox="0 0 140 140">
    <defs><linearGradient id="ring" x1="0" y1="0" x2="1" y2="1"><stop offset="0" stop-color="#5fe0ee"/><stop offset="1" stop-color="#6d6fd0"/></linearGradient></defs>
    <circle cx="70" cy="70" r="67" fill="none" stroke="url(#ring)" stroke-width="2.5"/>
    <circle cx="70" cy="70" r="50" fill="#0c4468" role="img" aria-label="Icon of a house-call car with a medical emblem"/>
  </svg>
</section>

<section class="intro">
  <h2>Not in our service area?</h2>
  <p>Call us and let us know you want Lumen Health to come to you.</p>
</section>
<div class="zip-search">
  <label for="zip">Zip Codes</label>
  <input id="zip" type="text" value="27617">
</div>

<div class="coverage-map" role="img" aria-label="Map of the zip code areas covered by the service"></div>

<section class="subscribe">
  <h2>Subscribe</h2>
  <input class="field-name" type="text" placeholder="Enter Name">
  <input class="field-email" type="email" placeholder="Enter Email Address">
  <button type="button">SUBSCRIBE NOW</button>
</section>

<footer class="site-footer">
  <nav class="footer-nav">
    <a href="#">HOME</a><a href="#">ABOUT US</a><a href="#">WHY LUMEN?</a><a href="#">SERVICE AREA</a><a href="#">OTHER</a><a href="#">CONTACT US</a>
  </nav>
  <p class="copyright">Copyright © 2019.&nbsp; Company Name&nbsp; All Rights Reserved</p>
  <div class="social"><span></span><span></span><span></span><span></span><span></span></div>
</footer>
</body>
</html>
```